Stylish Business Cards Wanted

- DOUBLE SIDED Design Required -

High end, edgy cards for a corporate and personal stylist. Must include logo,
Name: Belinda Harwick
Title: Director and Stylist
telephone : +61 8 7142 5809
email: belinda@theloombriefing.example
website: theloombriefing.example
Tag: Corporate Workwear & Uniform Specialist | Personal Stylist
Would like nice icons for telephone, email, website

Target Market(s)

Businesses wanting stylish uniforms, people wanting stylish wardrobes

Industry/Entity Type

Corporate Workwear Stylist

Contact Information for Business Card

I would like black, white and gold foiling incorporated in the design - possibly a touch of the other colours on my branding guide attached Name: Belinda Harwick Title: Director and Stylist telephone : +61 8 7142 5809 email: belinda@theloombriefing.example website: theloombriefing.example Tag: Corporate Workwear & Uniform Specialist | Personal Stylist Would like nice icons for telephone, email, website

Font styles to use
Other font styles liked:
• Raleway

Colors

Designer to choose colors to be used in the design.

Requirements
Must have
• Gold foil accents

```html
<!DOCTYPE html>
<html lang="en">
<head>
<meta charset="utf-8">
<title>The Loom Briefing – Business Cards</title>
<link rel="stylesheet" href="https://fonts.googleapis.com/css2?family=Great+Vibes&family=Raleway:wght@500;700&display=swap">
<style>
  :root {
    --backdrop: #e9e9e8;
    --card-white: #fafaf9;
    --card-black: #1f1f1f;
    --ink: #161616;
    --gold: #c9a23f;
    --emboss: #2e2e2e;
    --rule: #3a3a3a;
  }
  * { box-sizing: border-box; margin: 0; padding: 0; }
  html, body {
    width: 1200px; height: 801px; overflow: hidden;
    background: var(--backdrop);
    font-family: "Raleway", Arial, sans-serif;
  }
  .sheet {
    position: relative; width: 1200px; height: 801px;
    display: flex; align-items: center; justify-content: center; gap: 40px;
  }
  .card {
    position: relative; width: 540px; height: 309px;
    box-shadow: 0 10px 24px rgba(0,0,0,.18);
    overflow: hidden;
  }
  /* Front */
  .card--front { background: var(--card-white); color: var(--ink); }
  .brand {
    position: absolute; left: 0; right: 0; top: 58px;
    display: flex; align-items: center; justify-content: center; gap: 12px;
  }
  .brand__mark { width: 14px; height: 14px; background: var(--gold); }
  .brand__name {
    font-weight: 700; font-size: 34px; letter-spacing: 1px; color: var(--ink);
  }
  .details {
    position: absolute; left: 0; right: 0; top: 178px;
    display: flex; justify-content: center; align-items: center;
  }
  .person { text-align: right; padding-right: 20px; }
  .person__name {
    font-family: "Great Vibes", cursive; font-size: 36px; color: var(--gold); line-height: 1;
  }
  .person__title { font-size: 13px; font-weight: 500; margin-top: 4px; }
  .divider { width: 1px; height: 72px; background: var(--rule); }
  .contact { list-style: none; padding-left: 18px; font-size: 12px; font-weight: 500; }
  .contact li { display: flex; align-items: center; gap: 7px; line-height: 21px; }
  .contact svg { width: 11px; height: 11px; fill: var(--gold); flex: none; }
  .contact .accent { color: var(--gold); }
  /* Back */
  .card--back { background: var(--card-black); }
  .back-name {
    position: absolute; inset: 0;
    display: flex; align-items: center; justify-content: center;
    font-weight: 700; font-size: 54px; letter-spacing: 2px; color: var(--emboss);
  }
</style>
</head>
<body>
<main class="sheet">
  <section class="card card--front" aria-label="Card front">
    <div class="brand">
      <span class="brand__mark"></span>
      <span class="brand__name">The Loom Briefing</span>
    </div>
    <div class="details">
      <div class="person">
        <p class="person__name">Belinda Harwick</p>
        <p class="person__title">Director and Stylist</p>
      </div>
      <div class="divider"></div>
      <ul class="contact">
        <li>
          <svg viewBox="0 0 24 24" aria-hidden="true"><path d="M6.6 10.8a15 15 0 0 0 6.6 6.6l2.2-2.2a1 1 0 0 1 1-.25 11.4 11.4 0 0 0 3.6.57 1 1 0 0 1 1 1V20a1 1 0 0 1-1 1A17 17 0 0 1 3 4a1 1 0 0 1 1-1h3.5a1 1 0 0 1 1 1c0 1.25.2 2.45.57 3.6a1 1 0 0 1-.25 1z"/></svg>
          +61 8 7142 5809
        </li>
        <li>
          <svg viewBox="0 0 24 24" aria-hidden="true"><path d="M2 5h20v14H2z M2 5l10 8 10-8" fill="none" stroke="#c9a23f" stroke-width="2.4"/></svg>
          belinda@theloombriefing.example
        </li>
        <li>
          <svg viewBox="0 0 24 24" aria-hidden="true"><circle cx="12" cy="12" r="10" fill="none" stroke="#c9a23f" stroke-width="2.4"/><path d="M2 12h20M12 2c3 3 3 17 0 20M12 2c-3 3-3 17 0 20" fill="none" stroke="#c9a23f" stroke-width="2"/></svg>
          www.<span class="accent">theloombriefing.example</span>
        </li>
      </ul>
    </div>
  </section>

  <section class="card card--back" aria-label="Card back">
    <p class="back-name">The Loom Briefing</p>
  </section>
</main>
</body>
</html>
```